Foot doctor needs feet friendly business cards.

Business cards for Podiatrist. Needs to look professional and modern. Back side put an appointment card, and try to put a little basic street map somewhere on card along with all of our contact info below:

Marcus Dovan, DPM, Inc.
Diplomate, National Council of Lower Limb Medicine
Call: 1.877.Toes.482
1.555.283.9146
Fax: 1.555.671.3820
Email: info@DrDovanclinic.example
Web: www.DrDovanclinic.example
2847 W. Harbor Ln. Suite 204
Costa Mesa, CA 90000

```html
<!DOCTYPE html>
<html lang="en">
<head>
<meta charset="utf-8">
<title>Marcus Dovan, DPM, Inc. – Business Card</title>
<link href="https://fonts.googleapis.com/css2?family=Source+Sans+3:wght@400;600;700&display=swap" rel="stylesheet">
<style>
  :root {
    --card-bg-top: #1e1e1e;
    --card-bg-bottom: #0e0e0e;
    --text-main: #f2f2f2;
    --text-soft: #ffffff;
    --accent-red: #d60000;
    --rule: #8a8a8a;
    --rule-pink: #c98a9a;
    --feet-light: #ffffff;
    --feet-shade: #dcdcdc;
  }
  html, body {
    margin: 0;
    padding: 0;
    width: 1200px;
    height: 722px;
    overflow: hidden;
    background: #000;
  }
  .card {
    position: relative;
    width: 1200px;
    height: 722px;
    overflow: hidden;
    background: linear-gradient(160deg, var(--card-bg-top) 0%, var(--card-bg-bottom) 100%);
    font-family: "Source Sans 3", "Myriad Pro", Arial, sans-serif;
    color: var(--text-main);
  }
  .doctor-name {
    position: absolute;
    left: 40px;
    top: 70px;
    margin: 0;
    font-size: 84px;
    font-weight: 600;
    letter-spacing: -1px;
    line-height: 1;
    color: var(--text-main);
  }
  .practice-suffix {
    position: absolute;
    left: 460px;
    top: 174px;
    font-size: 39px;
    font-weight: 400;
    line-height: 1;
    color: var(--text-main);
  }
  .specialty {
    position: absolute;
    left: 42px;
    top: 246px;
    margin: 0;
    font-size: 25.5px;
    font-weight: 600;
    line-height: 1;
    color: var(--text-soft);
  }
  .medical-cross {
    position: absolute;
    left: 885px;
    top: 51px;
    width: 199px;
    height: 201px;
  }
  .feet-artwork {
    position: absolute;
    left: 210px;
    top: 345px;
    width: 281px;
    height: 260px;
    border-radius: 40px;
    background: radial-gradient(ellipse at center, var(--feet-light) 0%, var(--feet-shade) 100%);
  }
  .contact-rule {
    position: absolute;
    left: 859px;
    width: 254px;
    height: 1px;
    background: var(--rule);
  }
  .contact-rule.is-pink { background: var(--rule-pink); }
  .contact-icon {
    position: absolute;
    left: 797px;
    width: 42px;
    height: 42px;
  }
  .contact-text {
    position: absolute;
    color: var(--text-soft);
    line-height: 1.35;
    text-align: center;
  }
  .contact-fax { left: 870px; top: 315px; width: 230px; font-size: 21px; font-weight: 600; }
  .contact-phone { left: 870px; top: 392px; width: 230px; font-size: 21px; font-weight: 600; line-height: 1.45; }
  .contact-web { left: 845px; top: 482px; width: 290px; font-size: 20px; font-weight: 600; line-height: 1.45; }
  .contact-address { left: 873px; top: 574px; font-size: 18.5px; font-weight: 400; text-align: left; line-height: 1.4; }
  .board-credential {
    position: absolute;
    left: 0;
    top: 668px;
    width: 1194px;
    margin: 0;
    text-align: center;
    font-size: 31px;
    font-weight: 600;
    line-height: 1;
    color: var(--text-soft);
  }
</style>
</head>
<body>
<main class="card">
  <h1 class="doctor-name">Marcus Dovan</h1>
  <span class="practice-suffix">DPM, Inc.</span>
  <p class="specialty">Nail Fungus Laser Treatments and Heel pain relief specialist</p>

  <svg class="medical-cross" viewBox="0 0 199 201" aria-hidden="true">
    <rect x="70" y="0" width="58" height="201" fill="var(--accent-red)"/>
    <rect x="0" y="72" width="199" height="58" fill="var(--accent-red)"/>
  </svg>

  <div class="feet-artwork" role="img" aria-label="Illustration of two bare footprints"></div>

  <div class="contact-rule" style="top:285px"></div>
  <div class="contact-rule" style="top:377px"></div>
  <div class="contact-rule" style="top:466px"></div>
  <div class="contact-rule is-pink" style="top:555px"></div>
  <div class="contact-rule" style="top:643px"></div>

  <!-- fax icon -->
  <svg class="contact-icon" style="top:309px" viewBox="0 0 42 42" aria-hidden="true">
    <rect x="2" y="2" width="38" height="38" rx="8" fill="none" stroke="#fff" stroke-width="3"/>
    <rect x="13" y="9" width="15" height="9" fill="#fff"/>
    <rect x="10" y="17" width="22" height="15" rx="2" fill="#fff"/>
    <rect x="14" y="21" width="14" height="2" fill="#1a1a1a"/>
    <rect x="14" y="25" width="14" height="2" fill="#1a1a1a"/>
  </svg>
  <div class="contact-text contact-fax">1.555.671.3820</div>

  <!-- phone icon -->
  <svg class="contact-icon" style="top:391px" viewBox="0 0 42 42" aria-hidden="true">
    <rect x="2" y="2" width="38" height="38" rx="8" fill="none" stroke="#fff" stroke-width="3"/>
    <path d="M14 11 l4 0 l2 6 l-3 2 q2 5 7 7 l2 -3 l6 2 l0 4 q-1 3 -4 3 q-10 -1 -16 -11 q-2 -5 2 -10z" fill="#fff"/>
  </svg>
  <div class="contact-text contact-phone">1 877 869 3482<br>1.555.283.9146</div>

  <!-- globe icon -->
  <svg class="contact-icon" style="top:490px" viewBox="0 0 42 42" aria-hidden="true">
    <rect x="2" y="2" width="38" height="38" rx="8" fill="none" stroke="#fff" stroke-width="3"/>
    <circle cx="21" cy="21" r="11" fill="#fff"/>
    <path d="M15 15 q4 -2 6 1 q-1 3 -4 3 q-1 3 2 5 q-2 3 -4 0z M24 24 q3 -2 5 1 q-1 3 -4 3z" fill="#1a1a1a"/>
  </svg>
  <div class="contact-text contact-web">info@DrDovanclinic.example<br>www.DrDovanclinic.example</div>

  <!-- home icon -->
  <svg class="contact-icon" style="top:590px" viewBox="0 0 42 42" aria-hidden="true">
    <rect x="2" y="2" width="38" height="38" rx="8" fill="none" stroke="#fff" stroke-width="3"/>
    <path d="M9 21 L21 10 L33 21 L30 21 L30 31 L12 31 L12 21z" fill="#fff"/>
    <rect x="15" y="23" width="4" height="4" fill="#1a1a1a"/>
    <rect x="23" y="23" width="4" height="4" fill="#1a1a1a"/>
  </svg>
  <div class="contact-text contact-address">2847 W. Harbor Ln. Suite 204<br>Costa Mesa, CA 90000</div>

  <p class="board-credential">DIPLOMAT, NATIONAL COUNCIL OF LOWER LIMB MEDICINE</p>
</main>
</body>
</html>
```